Business card for Luxury Portable Restroom Trailer company

We are a Luxury Portable Restroom Trailer Company Called FALCRIDGE HIRES. Based in Orange County California. We provide portable restroom trailers for events, such as, Weddings, Concerts, Charity events, Sporting events, Tournaments, Corporate events, ect. We rent and Sell the Luxury restrooms. Our colors are white, grey, and Orange. As you will see in the logo we uploaded.
There are 2 people in the company so the names and titles will change for the 3 people but card will remain the same. Here is the information for each Person: Dwight Penner CFO 555 318-0476
next Person: Leon Marchetti VP 555 318-0476
Next Person: Owen Marchetti CEO 555 318-0476
Information to include on the card: Luxury Restroom Trailers Rental and Sales. Weddings, Concerts, Charity, Sporting and Corp. Events.

```html
<!DOCTYPE html>
<html lang="en">
<head>
<meta charset="utf-8">
<title>Falcridge Hires – Business Card</title>
<link href="https://fonts.googleapis.com/css2?family=Montserrat:wght@400;500;700;800&display=swap" rel="stylesheet">
<style>
  :root {
    --orange: #f26b24;
    --orange-deep: #e85d17;
    --white: #ffffff;
    --ink: #2b2b2b;
    --backdrop: #26262b;
  }
  * { margin: 0; padding: 0; box-sizing: border-box; }
  html, body { width: 1200px; height: 900px; overflow: hidden; }
  body {
    background: var(--backdrop);
    font-family: "Montserrat", sans-serif;
    position: relative;
  }
  .card {
    position: absolute;
    width: 560px;
    height: 320px;
    border-radius: 22px;
    overflow: hidden;
    box-shadow: 0 18px 40px rgba(0,0,0,.45);
  }
  .card-back {
    left: 320px; top: 100px;
    background: var(--orange);
    display: flex; flex-direction: column; align-items: center; justify-content: center;
    gap: 22px;
  }
  .brand {
    display: flex; align-items: center; gap: 16px;
    color: var(--white);
    font-weight: 800;
    letter-spacing: .04em;
  }
  .brand-mark { width: 34px; height: 34px; background: var(--white); flex: none; }
  .brand-name { font-size: 38px; line-height: 1; white-space: nowrap; }
  .services {
    color: var(--white);
    font-size: 12.5px;
    font-weight: 500;
    line-height: 1.6;
    text-align: center;
    letter-spacing: .02em;
  }

  .card-front {
    left: 320px; top: 480px;
    background: var(--white);
  }
  .feature-area {
    position: absolute; left: 0; top: 0;
    width: 230px; height: 320px;
    background: linear-gradient(160deg, var(--orange) 0%, var(--orange-deep) 100%);
  }
  .details {
    position: absolute; left: 270px; top: 34px; width: 270px;
    color: var(--ink);
  }
  .brand-small { gap: 8px; color: var(--orange); margin-bottom: 26px; }
  .brand-small .brand-mark { width: 16px; height: 16px; background: var(--orange); }
  .brand-small .brand-name { font-size: 18px; }
  .person-name { color: var(--orange); font-weight: 700; font-size: 22px; line-height: 1.1; }
  .person-title { font-size: 12px; font-weight: 500; margin-bottom: 14px; }
  .address { font-size: 11.5px; line-height: 1.45; margin-bottom: 14px; }
  .contacts { list-style: none; font-size: 11.5px; line-height: 1.75; }
  .contacts li { display: flex; align-items: center; gap: 8px; }
  .contacts svg { width: 12px; height: 12px; fill: var(--orange); flex: none; }
</style>
</head>
<body>

<section class="card card-back">
  <div class="brand">
    <span class="brand-mark"></span>
    <span class="brand-name">FALCRIDGE HIRES</span>
  </div>
  <p class="services">Luxury Restroom Trailers Rental and Sales<br>Weddings, Concerts, Charity, Sporting and Corp. Events</p>
</section>

<section class="card card-front">
  <div class="feature-area" role="img" aria-label="Large orange brand illustration bleeding off the left edge"></div>
  <div class="details">
    <div class="brand brand-small">
      <span class="brand-mark"></span>
      <span class="brand-name">FALCRIDGE HIRES</span>
    </div>
    <p class="person-name">Owen Marchetti</p>
    <p class="person-title">CEO</p>
    <p class="address">418 Harbor Crest Ave, #112<br>Irvine, CA 92614</p>
    <ul class="contacts">
      <li><svg viewBox="0 0 24 24"><path d="M6.6 10.8a15 15 0 0 0 6.6 6.6l2.2-2.2c.3-.3.7-.4 1-.2 1.1.4 2.3.6 3.6.6.6 0 1 .4 1 1V20c0 .6-.4 1-1 1A17 17 0 0 1 3 4c0-.6.4-1 1-1h3.5c.6 0 1 .4 1 1 0 1.3.2 2.5.6 3.6.1.3 0 .7-.2 1z"/></svg>555 318-0476</li>
      <li><svg viewBox="0 0 24 24"><path d="M7 1h10a2 2 0 0 1 2 2v18a2 2 0 0 1-2 2H7a2 2 0 0 1-2-2V3a2 2 0 0 1 2-2zm0 3v14h10V4zm5 15.5a1 1 0 1 0 0 2 1 1 0 0 0 0-2z"/></svg>555 318-0476</li>
      <li><svg viewBox="0 0 24 24"><path d="M2 5h20v14H2zm2 2v.5l8 5 8-5V7z"/></svg>info@falcridgehires.com</li>
      <li><svg viewBox="0 0 24 24"><path d="M12 2a10 10 0 1 0 0 20 10 10 0 0 0 0-20zm0 2c.9 1.2 1.6 2.6 2 4h-4c.4-1.4 1.1-2.8 2-4zM4.3 14a8 8 0 0 1 0-4h3.4a16 16 0 0 0 0 4zm5.7 0a14 14 0 0 1 0-4h4a14 14 0 0 1 0 4zm6.3 0a16 16 0 0 0 0-4h3.4a8 8 0 0 1 0 4z"/></svg>www.falcridgehires.com</li>
    </ul>
  </div>
</section>

</body>
</html>
```